Business card

We need a business card design for our company based in Auckland , New Zealand called 'Ridge + Studio Ltd'. We provide architectural services. We would like to see designs that use the max. three colours (such as white, black, grey) The final design should communicate financial safety and growth."
Also I will provide our company logo. I would like to the logo to be embeded onto our business card.

Target Market(s)

new residential house, alteration & addition & light commericila design & drafting service

Industry/Entity Type

Architecture

Contact Information for Business Card

Company name: ridge + studio Ltd.
Name: Mark Delford
Job title: architectural designer & Design LBP
email address: mark@rplusd.co.nz
mobile number: 02 5163 2290
web site: www.rplusd.co.nz

Requirements
Must have
• My project must have..
• - embeded logo (attached company logo)
• I don't have a bigger version for our company logo, but I have one old one, so you can remove the word from it)
• - insert the attached small BKTW logo & LBP logo
• - creative, simple and clear business card.
• - Max. three colours
Nice to have
• - Here are the samples I would like to share with you: http://www.plimvora.com/blog/minimalistic-business-card-designs/
• I would like to have my business card like one of the creation.
Should not have
• TBA

```html
<!DOCTYPE html>
<html lang="en">
<head>
<meta charset="utf-8">
<title>Ridge + Studio Ltd — Business Card</title>
<link href="https://fonts.googleapis.com/css2?family=Playfair+Display:wght@500&family=Libre+Caslon+Text:wght@400&family=Marcellus+SC&family=Lato:wght@400;700&display=swap" rel="stylesheet">
<style>
  :root {
    --canvas: #ffffff;
    --card-back: #d4d8d6;
    --card-front: #ffffff;
    --ink: #1c1c1c;
    --muted: #a4aaa7;
    --sage: #7f978a;
    --rule: #b9bebb;
    --badge: #1f1f1f;
  }
  html, body {
    margin: 0;
    width: 1200px;
    height: 1200px;
    overflow: hidden;
    background: var(--canvas);
  }
  .canvas {
    position: relative;
    width: 1200px;
    height: 1200px;
  }
  .card {
    position: absolute;
    box-shadow: 3px 5px 8px rgba(0,0,0,0.28);
  }
  .card--contact {
    left: 206px; top: 108px;
    width: 792px; height: 478px;
    background: var(--card-back);
  }
  .card--brand {
    left: 195px; top: 624px;
    width: 803px; height: 482px;
    background: var(--card-front);
  }

  /* Membership mark */
  .membership {
    position: absolute;
    left: 69px; top: 48px;
    font-family: "Lato", sans-serif;
    color: var(--sage);
  }
  .membership__name {
    font-size: 36px;
    font-weight: 700;
    letter-spacing: 1px;
    line-height: 1;
  }
  .membership__label {
    margin-top: 8px;
    font-size: 15px;
    font-weight: 700;
    line-height: 1.15;
  }
  .practitioner-badge {
    position: absolute;
    left: 70px; top: 300px;
    width: 110px; height: 110px;
    border-radius: 50%;
    background: var(--badge);
  }

  /* Contact block */
  .contact-rule {
    position: absolute;
    left: 391px; top: 163px;
    width: 1px; height: 161px;
    background: var(--rule);
  }
  .person {
    position: absolute;
    left: 425px; top: 158px;
  }
  .person__name {
    font-family: "Playfair Display", serif;
    font-weight: 500;
    font-size: 31px;
    color: var(--ink);
    margin: 0;
    line-height: 1.1;
  }
  .person__title {
    font-family: "Libre Caslon Text", serif;
    font-size: 15px;
    color: var(--muted);
    margin: 6px 0 0;
  }
  .contact-list {
    position: absolute;
    left: 425px; top: 252px;
    margin: 0;
    font-family: "Libre Caslon Text", serif;
    font-size: 14px;
    color: var(--ink);
    display: grid;
    grid-template-columns: 112px auto;
    row-gap: 11px;
  }
  .contact-list dt, .contact-list dd { margin: 0; }

  /* Brand face */
  .brand-mark {
    position: absolute;
    left: 130px; top: 164px;
    width: 138px; height: 138px;
    border-radius: 50%;
    border: 6px solid var(--ink);
    box-sizing: border-box;
  }
  .brand-rule {
    position: absolute;
    left: 327px; top: 202px;
    width: 1px; height: 79px;
    background: var(--rule);
  }
  .brand-name {
    position: absolute;
    left: 387px; top: 196px;
    margin: 0;
    font-family: "Marcellus SC", serif;
    font-weight: 400;
    font-size: 31px;
    line-height: 48px;
    color: var(--ink);
  }
</style>
</head>
<body>
<main class="canvas">
  <section class="card card--contact">
    <div class="membership">
      <div class="membership__name">BKTW</div>
      <div class="membership__label">Professional<br>Member</div>
    </div>
    <div class="practitioner-badge" aria-hidden="true"></div>

    <div class="contact-rule"></div>
    <div class="person">
      <h1 class="person__name">Mark Delford</h1>
      <p class="person__title">Architectural Designer &amp; Design LBP</p>
    </div>
    <dl class="contact-list">
      <dt>T</dt><dd>02 5163 2290</dd>
      <dt>M</dt><dd>mark@rplusd.co.nz</dd>
      <dt>W</dt><dd>www.rplusd.co.nz</dd>
    </dl>
  </section>

  <section class="card card--brand">
    <div class="brand-mark" aria-hidden="true"></div>
    <div class="brand-rule"></div>
    <h2 class="brand-name">Ridge +<br>Studio Ltd</h2>
  </section>
</main>
</body>
</html>
```